Brivolt Technologies business card design

We need a business card designed with our new logo. it would be great if the card could communicate it is a technology based company.

Target Market(s)

system integrators

Industry/Entity Type

technology, IOT

Contact Information for Business Card

Name, designation, Address, telephone number, email address

Requirements
Must have
• logo and company name
Nice to have
• something to do with technology

```html
<!DOCTYPE html>
<html lang="en">
<head>
<meta charset="utf-8">
<title>Brivolt Technologies – Business Card</title>
<link rel="stylesheet" href="https://fonts.googleapis.com/css2?family=Poppins:wght@400;500;700&display=swap">
<style>
  :root {
    --page-bg: #1b1b1c;
    --card-bg: #3b3b3c;
    --card-edge: #f7941d;
    --accent: #f7941d;
    --text-light: #ffffff;
    --text-muted: #e6e6e6;
    --emboss: #2a2a2b;
  }
  * { box-sizing: border-box; margin: 0; padding: 0; }
  html, body {
    width: 1200px; height: 900px; overflow: hidden;
    background: var(--page-bg);
    font-family: "Poppins", sans-serif;
  }
  .sheet {
    width: 1200px; height: 900px;
    display: flex; flex-direction: column; align-items: center; justify-content: center;
    gap: 40px;
  }
  .card {
    width: 700px; height: 400px;
    background: var(--card-bg);
    border-radius: 18px;
    border-bottom: 3px solid var(--card-edge);
    box-shadow: 0 10px 28px rgba(0,0,0,.55);
    position: relative;
    display: flex; align-items: center;
  }
  /* front */
  .card-front { padding: 0 56px; }
  .brand {
    display: flex; align-items: center; gap: 12px;
    font-weight: 700; text-transform: uppercase; letter-spacing: 1px;
  }
  .brand-square { background: var(--accent); flex: none; }
  .card-front .brand { width: 300px; font-size: 22px; color: var(--text-light); line-height: 1.15; }
  .card-front .brand-square { width: 26px; height: 26px; }
  .divider {
    width: 2px; height: 150px; background: var(--accent);
    margin: 0 30px 0 10px; flex: none;
  }
  .contact { color: var(--text-muted); font-size: 15px; line-height: 1.55; }
  .contact-name {
    color: var(--accent); font-weight: 700; font-size: 21px;
    text-transform: uppercase; letter-spacing: .5px; line-height: 1.2;
  }
  .contact-role { text-transform: uppercase; font-size: 14px; margin-bottom: 4px; }
  .contact-line { display: flex; align-items: center; gap: 8px; }
  .contact-line svg { width: 13px; height: 13px; flex: none; }
  /* back */
  .card-back { justify-content: center; }
  .card-back .brand { font-size: 42px; color: var(--emboss); gap: 20px; }
  .card-back .brand-square { width: 46px; height: 46px; }
</style>
</head>
<body>
<main class="sheet">
  <section class="card card-front">
    <div class="brand">
      <span class="brand-square"></span>
      <span class="brand-name">Brivolt Technologies</span>
    </div>
    <div class="divider"></div>
    <div class="contact">
      <p class="contact-name">Daniel Harrow</p>
      <p class="contact-role">Director</p>
      <p>1472 Alder Lane</p>
      <p>Greenfield, OH 45123</p>
      <p class="contact-line">
        <svg viewBox="0 0 24 24" fill="none" stroke="var(--accent)" stroke-width="2.2"><path d="M5 3h4l2 5-3 2a12 12 0 0 0 6 6l2-3 5 2v4a2 2 0 0 1-2 2A17 17 0 0 1 3 5a2 2 0 0 1 2-2z"/></svg>
        (555) 318-4072
      </p>
      <p class="contact-line">
        <svg viewBox="0 0 24 24" fill="none" stroke="var(--accent)" stroke-width="2.2"><rect x="3" y="5" width="18" height="14" rx="1"/><path d="M3 6l9 7 9-7"/></svg>
        info@brivolttech.com
      </p>
      <p class="contact-line">
        <svg viewBox="0 0 24 24" fill="none" stroke="var(--accent)" stroke-width="2"><circle cx="12" cy="12" r="9"/><path d="M3 12h18M12 3c3 3 3 15 0 18M12 3c-3 3-3 15 0 18"/></svg>
        brivolttech.com
      </p>
    </div>
  </section>

  <section class="card card-back">
    <div class="brand">
      <span class="brand-square"></span>
      <span class="brand-name">Brivolt Technologies</span>
    </div>
  </section>
</main>
</body>
</html>
```